Meadowlark Pet friendspace

We need a friendspace page created allowing us to share customer success stories on friendspace.

We have basically a start up business that I need help with. This project is just for the friendspace page.

Our product is a frozen raw pet food that promotes weight control, less shedding, smaller stools and an overall better health. The product is in nugget form similar to what you would see in a steak shish kabob. I only share that with you in case you want to incorporate that in the design.

We have been in business for 17 years but all of our sales have been word of mouth. We are going to be launching an infomercial this summer and I need everything stated previously to be completed before we can launch the infomercial.

Your help is appreciated.

Sincerely,

Dale

Target Market(s)

Women between the ages of 30 & 60.

Industry/Entity Type

Weight

```html
<!DOCTYPE html>
<html lang="en">
<head>
<meta charset="utf-8">
<title>Meadowlark Pet – Social Page</title>
<link href="https://fonts.googleapis.com/css2?family=Dosis:wght@600;700&family=Open+Sans:wght@400;600;700&display=swap" rel="stylesheet">
<style>
  :root {
    --page-bg: #e9ebf0;
    --bar-blue: #41609e;
    --bar-edge: #2f4a82;
    --link-blue: #3b5998;
    --name-navy: #1c2a47;
    --panel-white: #ffffff;
    --tile-bg: #f4f5f8;
    --line: #d3d7e0;
    --muted: #9aa3b8;
    --ink-black: #050505;
    --edge-grey: #4a4a4a;
    --accent-orange: #e8731a;
    --text-white: #ffffff;
    --bar-text: #cfcfcf;
  }
  * { margin: 0; padding: 0; box-sizing: border-box; }
  html, body { width: 1200px; height: 659px; overflow: hidden; background: var(--page-bg); }
  body { position: relative; font-family: "Open Sans", sans-serif; }
  .abs { position: absolute; }

  /* top bar */
  .top-bar { left: 0; top: 0; width: 1200px; height: 41px; background: var(--bar-blue); border-bottom: 1px solid var(--bar-edge); }
  .site-name { left: 141px; top: 6px; font-weight: 700; font-size: 22px; color: var(--text-white); letter-spacing: -.5px; }
  .bar-icons { left: 250px; top: 12px; }
  .search-box { left: 335px; top: 11px; width: 377px; height: 24px; background: #fff; border: 1px solid var(--bar-edge); font-size: 12px; color: #777; padding: 3px 6px; }
  .search-btn { position: absolute; right: 0; top: 0; width: 24px; height: 22px; border-left: 1px solid #ccc; }
  .user-thumb { left: 1044px; top: 10px; width: 25px; height: 26px; background: #c7cde0; border: 1px solid #fff; }
  .bar-link { top: 13px; font-size: 12px; font-weight: 700; color: var(--text-white); }
  .bar-divider { top: 12px; width: 1px; height: 18px; background: #6b83b6; }

  /* cover */
  .cover-art { left: 141px; top: 41px; width: 919px; height: 340px; display: block; }
  .diet-item { font-family: "Dosis", sans-serif; font-weight: 600; font-size: 46px; }
  .diet-item.is-accent { fill: var(--accent-orange); }
  .diet-item.is-plain { fill: var(--text-white); }
  .contact-text { font-family: "Open Sans", sans-serif; font-size: 12.5px; fill: var(--bar-text); }

  /* page header panel */
  .header-panel { left: 141px; top: 381px; width: 919px; height: 173px; background: var(--panel-white); border-bottom: 2px solid var(--line); }
  .page-name { left: 331px; top: 400px; font-size: 21px; font-weight: 700; color: var(--name-navy); }
  .message-btn { left: 907px; top: 400px; width: 126px; height: 26px; background: #f6f7f9; border: 1px solid #a9b2c4; display: flex; font-size: 13px; font-weight: 700; color: #333; }
  .message-btn .label { padding: 3px 9px; border-right: 1px solid #c8ced9; }
  .message-btn .options { flex: 1; display: flex; align-items: center; justify-content: center; }
  .tab-tile { top: 446px; height: 80px; background: var(--tile-bg); border: 1px solid #dfe2e9; }
  .tab-label { top: 533px; font-size: 12px; color: var(--link-blue); }
  .more-btn { left: 1015px; top: 476px; width: 31px; height: 20px; background: #fff; border: 1px solid #b3bac8; display: flex; align-items: center; justify-content: center; }
  .profile-frame { left: 164px; top: 283px; width: 150px; height: 150px; background: #fff; border: 1px solid #c9cdd6; padding: 5px; box-shadow: 0 1px 2px rgba(0,0,0,.15); }
  .brand-tile { width: 100%; height: 100%; background: #f7f1e8; display: flex; flex-direction: column; align-items: center; justify-content: center; gap: 8px; }
  .brand-mark { width: 18px; height: 18px; background: var(--accent-orange); }
  .brand-name { font-family: "Dosis", sans-serif; font-weight: 700; font-size: 20px; color: var(--ink-black); text-align: center; line-height: 1.05; }
  .brand-tagline { font-family: "Dosis", sans-serif; font-weight: 700; font-size: 8px; letter-spacing: .4px; color: var(--ink-black); }

  /* timeline */
  .timeline-line { left: 598px; top: 556px; width: 3px; height: 103px; background: #d0d5e0; }
  .highlights-pill { left: 558px; top: 572px; width: 84px; height: 24px; background: var(--page-bg); border: 1px solid #c5cbd8; border-radius: 3px; font-size: 12px; color: var(--muted); padding: 3px 8px; }
  .story-card { top: 613px; height: 50px; background: #fff; border: 1px solid #d6dae3; }

  /* sidebar */
  .admin-btn { left: 1073px; top: 55px; width: 91px; height: 22px; background: #fff; border: 1px solid #999; border-radius: 2px; font-size: 12px; font-weight: 700; color: #333; text-align: center; line-height: 20px; }
  .year-rail { left: 1074px; top: 93px; width: 2px; height: 146px; background: #d8dce5; }
  .year-rail-active { left: 1074px; top: 93px; width: 5px; height: 24px; background: var(--link-blue); }
  .year-item { left: 1086px; font-size: 11.5px; color: var(--muted); }
  .year-item.is-current { color: var(--link-blue); font-weight: 700; }
</style>
</head>
<body>
  <div class="abs top-bar"></div>
  <div class="abs site-name">friendspace</div>
  <svg class="abs bar-icons" width="80" height="18" viewBox="0 0 80 18" fill="#9fb0d6" aria-hidden="true">
    <circle cx="9" cy="5" r="4"/><path d="M2 17 q7 -10 14 0 z"/>
    <rect x="27" y="2" width="12" height="9" rx="1"/><rect x="33" y="6" width="12" height="9" rx="1"/>
    <circle cx="63" cy="9" r="8"/>
  </svg>
  <div class="abs search-box">Search<span class="search-btn"></span></div>
  <div class="abs user-thumb"></div>
  <div class="abs bar-link" style="left:1076px">Name</div>
  <div class="abs bar-divider" style="left:1120px"></div>
  <div class="abs bar-link" style="left:1129px">Home</div>
  <div class="abs bar-divider" style="left:1175px"></div>
  <svg class="abs" style="left:1182px;top:19px" width="10" height="6" aria-hidden="true"><path d="M0 0 h10 l-5 6 z" fill="#fff"/></svg>

  <svg class="abs cover-art" viewBox="0 0 850 315" xmlns="http://www.w3.org/2000/svg">
    <defs>
      <linearGradient id="dogBowlTones" x1="0" y1="0" x2="1" y2="1">
        <stop offset="0" stop-color="#f4efe9"/><stop offset=".55" stop-color="#d9b79a"/><stop offset="1" stop-color="#c4282a"/>
      </linearGradient>
      <linearGradient id="walkTones" x1="0" y1="0" x2="1" y2="1">
        <stop offset="0" stop-color="#b9b4ab"/><stop offset=".6" stop-color="#c65a78"/><stop offset="1" stop-color="#5b5750"/>
      </linearGradient>
    </defs>
    <rect width="850" height="315" fill="var(--ink-black)"/>
    <g role="img" aria-label="Photo of a bulldog puppy eating from a red bowl">
      <path d="M0 0 H250 C228 90 285 185 236 285 H0 Z" fill="url(#dogBowlTones)"/>
    </g>
    <path d="M250 0 C228 90 285 185 236 285" fill="none" stroke="var(--edge-grey)" stroke-width="7"/>
    <g role="img" aria-label="Photo of a smiling woman kneeling beside her boxer dog on a sidewalk">
      <path d="M642 0 H850 V285 H612 C665 205 600 110 642 0 Z" fill="url(#walkTones)"/>
    </g>
    <path d="M642 0 C600 110 665 205 612 285" fill="none" stroke="var(--edge-grey)" stroke-width="7"/>
    <g fill="var(--text-white)">
      <path d="M306 60 h13 v-7 l13 11 l-13 11 v-7 h-13 z"/>
      <path d="M306 114 h13 v-7 l13 11 l-13 11 v-7 h-13 z"/>
      <path d="M306 168 h13 v-7 l13 11 l-13 11 v-7 h-13 z"/>
      <path d="M306 222 h13 v-7 l13 11 l-13 11 v-7 h-13 z"/>
    </g>
    <text class="diet-item is-accent" x="346" y="78" textLength="246" lengthAdjust="spacingAndGlyphs">Combination Diet</text>
    <text class="diet-item is-plain" x="346" y="132" textLength="171" lengthAdjust="spacingAndGlyphs">Chiken&#160; Diet</text>
    <text class="diet-item is-accent" x="346" y="186" textLength="130" lengthAdjust="spacingAndGlyphs">Beef Diet</text>
    <text class="diet-item is-plain" x="346" y="240" textLength="142" lengthAdjust="spacingAndGlyphs">Lamb Diet</text>
    <rect y="285" width="850" height="30" fill="var(--ink-black)"/>
    <g fill="none" stroke="var(--bar-text)" stroke-width="1.2">
      <circle cx="180" cy="301" r="7"/><path d="M176 298 l2 6 l2 -4 l2 4 l2 -6"/>
      <circle cx="379" cy="301" r="7"/><path d="M376 297 q-1 5 4 8 l1.5 -1.5 l-2 -2 l-1 1 q-2 -1.5 -2 -3.5 l1 -1 l-1.5 -2 z"/>
      <circle cx="531" cy="301" r="7"/><rect x="527" y="298" width="8" height="6"/><path d="M527 298 l4 3 l4 -3"/>
    </g>
    <text class="contact-text" x="195" y="305">www.websitename.com</text>
    <text class="contact-text" x="394" y="305">000-000-0000</text>
    <text class="contact-text" x="548" y="305">companyname@mail.com</text>
  </svg>

  <div class="abs header-panel"></div>
  <div class="abs page-name">Name</div>
  <div class="abs message-btn"><span class="label">Message</span><span class="options">
    <svg width="24" height="10" viewBox="0 0 24 10" aria-hidden="true"><circle cx="5" cy="5" r="4" fill="none" stroke="#555" stroke-width="2"/><path d="M15 3 h8 l-4 5 z" fill="#4a64a0"/></svg></span></div>

  <div class="abs tab-tile" style="left:141px;width:354px"></div>
  <svg class="abs" style="left:168px;top:454px" width="11" height="11" aria-hidden="true"><path d="M1 1 h5 l4 4 l-5 5 l-4 -4 z" fill="#6b6f78"/></svg>
  <div class="abs tab-tile" style="left:503px;width:120px"></div>
  <div class="abs tab-tile" style="left:632px;width:120px"></div>
  <div class="abs" style="left:681px;top:476px;width:20px;height:20px;background:#6d84b4"></div>
  <div class="abs tab-tile" style="left:761px;width:120px"></div>
  <div class="abs tab-tile" style="left:889px;width:120px"></div>
  <div class="abs tab-tile" style="left:1019px;width:41px;border-right:none"></div>
  <div class="abs more-btn"><svg width="10" height="6" aria-hidden="true"><path d="M0 0 h10 l-5 6 z" fill="#4a64a0"/></svg></div>
  <div class="abs tab-label" style="left:187px">About</div>
  <div class="abs tab-label" style="left:503px">Photos</div>
  <div class="abs tab-label" style="left:632px">Likes</div>
  <div class="abs tab-label" style="left:761px">Tab1</div>
  <div class="abs tab-label" style="left:889px">Tab2</div>

  <div class="abs profile-frame">
    <div class="brand-tile">
      <span class="brand-mark"></span>
      <span class="brand-name">Meadowlark Pet</span>
      <span class="brand-tagline">100% NATURAL RAW DOG FOOD</span>
    </div>
  </div>

  <div class="abs timeline-line"></div>
  <div class="abs highlights-pill">Highlights ▾</div>
  <div class="abs story-card" style="left:141px;width:443px"></div>
  <div class="abs story-card" style="left:616px;width:444px"></div>

  <div class="abs admin-btn">Admin Panel</div>
  <div class="abs year-rail"></div>
  <div class="abs year-rail-active"></div>
  <div class="abs year-item is-current" style="top:97px">Now</div>
  <div class="abs year-item" style="top:122px">Date</div>
  <div class="abs year-item" style="top:147px">Date</div>
  <div class="abs year-item" style="top:172px">Date</div>
  <div class="abs year-item" style="top:196px">Date</div>
  <div class="abs year-item" style="top:221px">Joined friendspace</div>
</body>
</html>
```